Media Services Start-up -- Corporate Website and Logo Design. Inspiration required!

We need a logo design and corporate website design, including coding, for our start-up business.
Vennatra’s value proposition is based on bringing together media content from a vast number of geographies globally, adding human and AI curation, translation and editing, and delivering the content using tailored customer interfaces. On the one hand, the business brings together media coverage from all over the world, and on the other it brings together content, human skills and technology to deliver a supreme customer experience.
Vennatra is a B2B media monitoring and analytics business with emphasis on global customers. Vennatra's service offering is centred around sourcing media content from different markets, processing, storing and delivering the content and insights derived from it using an online platform / mobile app.
The messaging we want to create through the logo is:
- Global scope
- Speed of delivery
- Cost-efficiency
- Multi-lingual
- Tailor-made
- Trustworthy
Target Market(s)
Business to business, PR / Communications, Media, Marketing
Logo Text
Vennatra
Coding
Coded - Design and coding required
Number of Pages Required
5+ page
Font styles to use
Other font styles liked:
- See Design Brief for details
Colors
Designer to choose colors to be used in the design.

```html
<!DOCTYPE html>
<html lang="en">
<head>
<meta charset="utf-8">
<meta name="format-detection" content="telephone=no,email=no,address=no">
<title>Vennatra – Website Pages</title>
<link href="https://fonts.googleapis.com/css2?family=Roboto:wght@300;400;500;700;900&family=Roboto+Condensed:wght@300;700&family=Open+Sans:wght@400&display=swap" rel="stylesheet">
<style>
:root{
  --teal:#20c6c9;
  --ink:#111;
  --white:#fff;
  --hero-dark:#3a3d44;
  --hero-warm:#6b5a52;
  --card:#e6e6e7;
  --section-dark:#242424;
  --footer:#050505;
  --muted:#d8d8d8;
  --field-text:#777;
}
*{margin:0;padding:0;box-sizing:border-box}
html,body{width:687px;height:1200px;overflow:hidden}
body{background:var(--teal);position:relative;font-family:"Roboto",sans-serif;color:var(--ink)}
a{color:inherit;text-decoration:none}
.page{position:absolute;left:66px;width:566px;background:var(--white);overflow:hidden}
.page--home{top:42px;height:519px}
.page--solutions{top:581px;height:564px}

.site-header{position:relative;height:54px;background:var(--white);display:flex;align-items:center;justify-content:space-between;padding:0 53px}
.brand{display:flex;align-items:center;gap:4px;font-family:"Roboto Condensed",sans-serif;font-weight:700;font-size:13px;letter-spacing:1.5px;color:var(--ink)}
.brand__dot{width:10px;height:10px;border-radius:50%;background:var(--teal)}
.brand--light{color:var(--white)}
.main-nav{display:flex;gap:20px;font-family:"Roboto",sans-serif;font-weight:900;font-size:7px;letter-spacing:.6px}
.main-nav a{color:var(--ink)}
.main-nav a.is-active{color:var(--teal)}

.hero{position:relative;height:317px;overflow:hidden}
.hero__photo{position:absolute;inset:0;background:linear-gradient(115deg,#4b4d54 0%,var(--hero-dark) 40%,var(--hero-warm) 70%,#4a4c52 100%)}
.hero__shade{position:absolute;inset:0;background:rgba(40,44,52,.45)}
.hero__copy{position:absolute;left:53px;top:68px;width:240px;color:var(--white)}
.hero__title{font-family:"Roboto Condensed",sans-serif;font-weight:700;font-size:25px;line-height:25px;letter-spacing:.6px}
.hero__subtitle{font-family:"Roboto Condensed",sans-serif;font-weight:300;font-size:22px;line-height:25px;letter-spacing:.3px}
.hero__lead{font-family:"Open Sans",sans-serif;font-size:9.6px;line-height:14px;margin-top:9px}
.btn-learn{position:absolute;left:53px;top:195px;width:103px;height:29px;border-radius:15px;background:var(--teal);color:var(--white);font-size:9.5px;font-weight:500;display:flex;align-items:center;justify-content:center}

.lead-card{position:absolute;left:318px;top:44px;width:195px;height:211px;background:var(--card);border-radius:12px}
.lead-card__title{position:absolute;left:25px;top:25px;font-size:10px;color:var(--ink)}
.lead-card__field{position:absolute;left:25px;width:146px;height:23px;background:var(--white);font-size:7px;color:var(--field-text);padding-left:11px;display:flex;align-items:center}
.lead-card__button{position:absolute;left:25px;top:149px;width:146px;height:28px;border:1.5px solid var(--ink);border-radius:14px;font-size:8.5px;font-weight:500;display:flex;align-items:center;justify-content:center}

.site-footer{position:absolute;left:0;bottom:0;width:566px;background:var(--footer);color:var(--white)}
.page--home .site-footer{height:148px}
.page--solutions .site-footer{height:145px}
.site-footer .brand{position:absolute;left:0;right:0;top:28px;justify-content:center}
.contact{position:absolute;top:60px;display:flex;align-items:center;gap:5px;font-size:8px;color:var(--white)}
.contact__icon{width:25px;height:25px;border:1px solid var(--white);border-radius:50%;display:flex;align-items:center;justify-content:center}
.contact--phone{left:54px}.contact--address{left:168px}.contact--email{left:402px}
.site-footer__rule{position:absolute;left:53px;right:53px;top:114px;height:1px;background:#555}
.site-footer__copy{position:absolute;left:0;right:0;top:127px;text-align:center;font-size:5.5px}

.services{position:relative;height:365px;background:var(--section-dark);color:var(--white)}
.service{position:absolute}
.service__icon{position:absolute;left:-26px;top:-6px;width:20px;height:20px;border-radius:50%;border:3.5px solid var(--teal)}
.service__title{font-family:"Roboto",sans-serif;font-weight:900;font-size:8px;letter-spacing:.7px;line-height:10px}
.service__text{font-size:6px;line-height:9.3px;margin-top:3px;color:var(--muted)}
.ticks{list-style:none;margin-top:5px}
.ticks li{position:relative;padding-left:6px;font-size:5.5px;line-height:6.8px;margin-bottom:5.5px;color:var(--muted)}
.ticks li::before{content:"";position:absolute;left:0;top:1.3px;width:2px;height:4px;border:solid var(--teal);border-width:0 1.2px 1.2px 0;transform:rotate(40deg)}
</style>
</head>
<body>

<section class="page page--home">
  <header class="site-header">
    <div class="brand"><span>VENNATRA</span><span class="brand__dot"></span></div>
    <nav class="main-nav">
      <a class="is-active">HOME</a><a>SOLUTIONS</a><a>HOW WE DO IT</a><a>OUR PEOPLE</a><a>OUR TECHNOLOGY</a>
    </nav>
  </header>

  <div class="hero">
    <div class="hero__photo" role="img" aria-label="Photo of a team working together at a desk with a laptop and charts"></div>
    <div class="hero__shade"></div>
    <div class="hero__copy">
      <h1 class="hero__title">DELIVERING GLOBAL</h1>
      <p class="hero__subtitle">MEDIA INTELLIGENCE</p>
      <p class="hero__lead">Vennatra is an international media intelligence service provider. We help communications teams build and operate truly global media monitoring and measurement programmes.</p>
    </div>
    <div class="btn-learn">LEARN MORE</div>

    <form class="lead-card">
      <p class="lead-card__title">Learn more about Vennatra</p>
      <div class="lead-card__field" style="top:53px">Name</div>
      <div class="lead-card__field" style="top:83px">Email</div>
      <div class="lead-card__field" style="top:113px">Phone</div>
      <div class="lead-card__button">GET STARTED</div>
    </form>
  </div>

  <footer class="site-footer">
    <div class="brand brand--light"><span>VENNATRA</span><span class="brand__dot"></span></div>
    <div class="contact contact--phone"><span class="contact__icon"><svg width="10" height="10" viewBox="0 0 24 24"><path fill="#fff" d="M6.6 10.8a15 15 0 0 0 6.6 6.6l2.2-2.2c.3-.3.7-.4 1-.2 1.1.4 2.3.6 3.6.6.6 0 1 .4 1 1V20c0 .6-.4 1-1 1A17 17 0 0 1 3 4c0-.6.4-1 1-1h3.5c.6 0 1 .4 1 1 0 1.3.2 2.5.6 3.6.1.3 0 .7-.2 1z"/></svg></span><span>012 345 6789</span></div>
    <div class="contact contact--address"><span class="contact__icon"><svg width="10" height="10" viewBox="0 0 24 24"><path fill="#fff" d="M12 3 2 12h3v8h5v-5h4v5h5v-8h3z"/></svg></span><span>Vennatra, Street Address, City Name, Country Code.</span></div>
    <div class="contact contact--email"><span class="contact__icon"><svg width="10" height="10" viewBox="0 0 24 24"><path fill="#fff" d="M12 3 2 12h3v8h5v-5h4v5h5v-8h3z"/></svg></span><span>info&#64;domainname&#46;com</span></div>
    <div class="site-footer__rule"></div>
    <p class="site-footer__copy">Copyrights © 2019 Vennatra. All rights reserved.</p>
  </footer>
</section>

<section class="page page--solutions">
  <header class="site-header">
    <div class="brand"><span>VENNATRA</span><span class="brand__dot"></span></div>
    <nav class="main-nav">
      <a>HOME</a><a class="is-active">SOLUTIONS</a><a>HOW WE DO IT</a><a>OUR PEOPLE</a><a>OUR TECHNOLOGY</a>
    </nav>
  </header>

  <div class="services">
    <article class="service" style="left:79px;top:30px;width:200px">
      <span class="service__icon"></span>
      <h2 class="service__title">CONTENT SOURCING</h2>
      <p class="service__text">We help you build a content strategy that meets your budget and coverage needs across earned media - Print, Online, TV and Radio.</p>
      <ul class="ticks">
        <li>Identify geographies and markets of interest</li>
        <li>Build target media source lists to fulfil monitoring and measurement requirements</li>
        <li>Using our transparent cost calculator, we help you with accurate budgeting and choices to ensure you meet your strategy and objectives</li>
      </ul>
    </article>

    <article class="service" style="left:79px;top:138px;width:196px">
      <span class="service__icon"></span>
      <h2 class="service__title">CONTENT COLLECTION</h2>
      <p class="service__text">We consolidate and manage the delivery of your global media content into a Cloud-based scalable media platform, taking the headache of content management away from your teams.</p>
    </article>

    <article class="service" style="left:79px;top:201px;width:222px">
      <span class="service__icon"></span>
      <h2 class="service__title">CONTENT AUGMENTATION</h2>
      <ul class="ticks">
        <li>We manage and normalise all of the source-level reference data - country, language, reach etc.</li>
        <li>We add editorial validation to ensure only the content required reaches your delivery, removing inevitable noise from source providers</li>
        <li>Tagging - AI and human based tagging to detect locations, people, topics, products, brands, services, etc.</li>
        <li>Human and automated grouping of stories across geographies - clustering, "also-in" groupings etc.</li>
        <li>Translation summarisation - AI Translation or human-created depending on budget, speed of delivery and need.</li>
        <li>Digest authoring - refining the essence of today's coverage into a concise board-ready output for your organisation</li>
      </ul>
    </article>

    <article class="service" style="left:342px;top:30px;width:174px">
      <span class="service__icon"></span>
      <h2 class="service__title">CONTENT DELIVERY</h2>
      <p class="service__text">Early morning delivery of a consolidated, ready-to-consume media coverage</p>
      <ul class="ticks">
        <li>Customised email templates, delivering content in templates designed to meet your needs</li>
        <li>Customised platform - modern portal tailored to meet your media management needs, removing the unwanted clutter and focusing on the job at hand</li>
        <li>Integration with Intranets, third-party communication tools e.g. Pingloom, RSS readers, customised APIs</li>
      </ul>
    </article>

    <article class="service" style="left:342px;top:151px;width:174px">
      <span class="service__icon"></span>
      <h2 class="service__title">MEDIA INSIGHTS &amp; CONSULTANCY</h2>
      <p class="service__text">Levering the normalised content sets from your integrated monitoring service, we can analyse and tag your coverage based on complex qualitative measurement criteria, consistent across all languages and geographies, to combine with quantitative metrics.</p>
      <ul class="ticks">
        <li>Ability to create a single consistent measurement programme across all of your global operations.</li>
        <li>Consultancy to HQ and local offices on how to utilise and align existing measurement and insight intiatives to provide continuity.</li>
        <li>Customised online dashboards with near real time data insights, coupled with Board-ready offline reporting and export options.</li>
        <li>Integration with social media content, third-party data, point-of-sale, Quillvane Stats, and delivering on your Integrated Communications Framework</li>
      </ul>
    </article>
  </div>

  <footer class="site-footer">
    <div class="brand brand--light"><span>VENNATRA</span><span class="brand__dot"></span></div>
    <div class="contact contact--phone"><span class="contact__icon"><svg width="10" height="10" viewBox="0 0 24 24"><path fill="#fff" d="M6.6 10.8a15 15 0 0 0 6.6 6.6l2.2-2.2c.3-.3.7-.4 1-.2 1.1.4 2.3.6 3.6.6.6 0 1 .4 1 1V20c0 .6-.4 1-1 1A17 17 0 0 1 3 4c0-.6.4-1 1-1h3.5c.6 0 1 .4 1 1 0 1.3.2 2.5.6 3.6.1.3 0 .7-.2 1z"/></svg></span><span>012 345 6789</span></div>
    <div class="contact contact--address"><span class="contact__icon"><svg width="10" height="10" viewBox="0 0 24 24"><path fill="#fff" d="M12 3 2 12h3v8h5v-5h4v5h5v-8h3z"/></svg></span><span>Vennatra, Street Address, City Name, Country Code.</span></div>
    <div class="contact contact--email"><span class="contact__icon"><svg width="10" height="10" viewBox="0 0 24 24"><path fill="#fff" d="M12 3 2 12h3v8h5v-5h4v5h5v-8h3z"/></svg></span><span>info&#64;domainname&#46;com</span></div>
    <div class="site-footer__rule"></div>
    <p class="site-footer__copy">Copyrights © 2019 Vennatra. All rights reserved.</p>
  </footer>
</section>

</body>
</html>
```